Dietitian needs awesome business card

I need a contemporary design that's eye catching but professional.
My card is to given to doctors, specialists and patients alike.
I manage patients with chronic diseases
I have uploaded my logo and current business card, I would also like the other Certified Clinical Nutritionist logo incorporated into the design

Target Market(s)

Doctors, specialists and patients

Industry/Entity Type

Healthcare

Contact Information for Business Card

www.brightfieldnutrition.com.au
Ph: 0427 561 903
Fax: 6457 2183
email: marcus.k.diet@fernmail.com
Space on the back of the card with: Appointment date, Appointment time and appointment location

Font styles to use
Serif

Colors
fbee3e
876aae
ffc214

Requirements
Must have
• My Logo
• Certified Clinical Nutritionist Logo
• My 4 locations - Pinebrook Medical Centre, North Corrin Health, Hollis Medical, Ashcombe Doctors Surgery
Nice to have
• I like the colours in my current business card

```html
<!DOCTYPE html>
<html lang="en">
<head>
<meta charset="utf-8">
<title>Brightfield Nutrition &amp; Dietetics – Business Card</title>
<link rel="stylesheet" href="https://fonts.googleapis.com/css2?family=Open+Sans:ital,wght@0,400;0,600;1,600&display=swap">
<style>
  :root {
    --canvas: #e9e7e4;
    --card-face: #f4f4f4;
    --card-white: #ffffff;
    --brand-navy: #1d3f95;
    --band-blue-top: #1a8bd6;
    --band-blue-bottom: #0f5fb5;
    --band-green-top: #a6d63a;
    --band-green-bottom: #6fb51f;
    --text-white: #ffffff;
    --appt-blue: #1f4aa8;
    --rule-grey: #5a6fa8;
    --badge-orange: #f26a21;
    --brand-green: #7cc242;
  }
  * { box-sizing: border-box; margin: 0; padding: 0; }
  html, body {
    width: 1200px; height: 900px; overflow: hidden;
    background: var(--canvas);
    font-family: "Open Sans", Arial, sans-serif;
  }
  .canvas { position: relative; width: 1200px; height: 900px; }

  .card {
    position: absolute;
    overflow: hidden;
    box-shadow: 0 6px 18px rgba(0,0,0,0.15);
  }

  /* Front */
  .card--front {
    left: 238px; top: 62px; width: 555px; height: 342px;
    background: var(--card-face);
  }
  .brand {
    position: absolute; left: 122px; top: 38px;
    display: flex; align-items: center; gap: 14px;
  }
  .brand__dot {
    width: 86px; height: 86px; border-radius: 50%;
    background: var(--brand-green);
  }
  .brand__name {
    color: var(--brand-navy); font-weight: 400; line-height: 1;
  }
  .brand__name-main { display: block; font-size: 40px; }
  .brand__name-sub { display: block; font-size: 17px; margin-top: 6px; }

  .contact-band {
    position: absolute; left: 0; top: 186px; width: 100%; height: 122px;
    background: linear-gradient(180deg, var(--band-blue-top), var(--band-blue-bottom));
    color: var(--text-white);
  }
  .contact-band__name {
    position: absolute; left: 44px; top: 56px;
    font-size: 18px; font-weight: 600;
  }
  .contact-list {
    position: absolute; left: 276px; top: 25px; list-style: none;
    font-size: 14.5px; line-height: 19.5px;
  }
  .contact-list li { display: flex; align-items: center; gap: 10px; }
  .contact-list svg { width: 11px; height: 11px; fill: var(--text-white); flex: none; }

  .title-band {
    position: absolute; left: 0; top: 308px; width: 100%; height: 34px;
    background: linear-gradient(180deg, var(--band-green-top), var(--band-green-bottom));
    color: var(--text-white); font-size: 15px; font-weight: 600;
    text-align: center; line-height: 34px; padding-left: 14px;
  }

  /* Back */
  .card--back {
    left: 458px; top: 518px; width: 559px; height: 344px;
    background: var(--card-face);
  }
  .back-mark {
    position: absolute; right: 130px; top: 40px;
    color: var(--brand-navy); opacity: 0.18; font-weight: 400;
    font-size: 40px; line-height: 1; text-align: right;
  }
  .back-mark small { display: block; font-size: 17px; margin-top: 6px; }

  .locations {
    position: absolute; left: 32px; top: 36px;
    color: var(--appt-blue); font-size: 13px; line-height: 20px;
  }
  .locations__heading { font-weight: 600; font-size: 13.5px; margin-bottom: 4px; }
  .locations__list { list-style: none; }

  .appointment {
    position: absolute; left: 0; top: 187px; width: 100%; height: 157px;
    background: var(--card-white);
  }
  .appointment__heading {
    position: absolute; left: 146px; top: 14px;
    color: var(--appt-blue); font-size: 17px; font-weight: 600;
  }
  .field {
    position: absolute; font-size: 14.5px; color: var(--appt-blue);
    display: flex; align-items: flex-end; gap: 8px;
  }
  .field__line { display: inline-block; border-bottom: 1px solid var(--rule-grey); height: 1px; margin-bottom: 3px; }
  .field--date { left: 32px; top: 54px; }
  .field--time { left: 205px; top: 54px; }
  .field--location { left: 32px; top: 78px; }
  .appointment__note {
    position: absolute; left: 32px; top: 119px;
    color: var(--appt-blue); font-size: 14.6px; font-style: italic; font-weight: 600;
  }
  .appointment__divider {
    position: absolute; left: 430px; top: 14px; width: 1px; height: 128px;
    background: var(--rule-grey);
  }
  .appointment__badge {
    position: absolute; left: 452px; top: 52px; width: 74px; height: 78px;
  }
</style>
</head>
<body>
<main class="canvas">

  <section class="card card--front" aria-label="Business card front">
    <div class="brand">
      <span class="brand__dot"></span>
      <span class="brand__name">
        <span class="brand__name-main">Brightfield</span>
        <span class="brand__name-sub">Nutrition &amp; Dietetics</span>
      </span>
    </div>

    <div class="contact-band">
      <p class="contact-band__name">Marcus Kellaway</p>
      <ul class="contact-list">
        <li><svg viewBox="0 0 24 24" aria-hidden="true"><path d="M6.6 10.8a15.1 15.1 0 0 0 6.6 6.6l2.2-2.2a1 1 0 0 1 1-.25 11.4 11.4 0 0 0 3.6.57 1 1 0 0 1 1 1V20a1 1 0 0 1-1 1A17 17 0 0 1 3 4a1 1 0 0 1 1-1h3.5a1 1 0 0 1 1 1c0 1.250.2 2.45.57 3.6a1 1 0 0 1-.25 1z"/></svg>0427 561 903</li>
        <li><svg viewBox="0 0 24 24" aria-hidden="true"><path d="M6 2h9v5H6zM3 8h18v12H3zm4 3v2h2v-2zm4 0v2h2v-2zm4 0v2h2v-2zm-8 4v2h2v-2zm4 0v2h2v-2zm4 0v2h2v-2z"/></svg>6457 2183</li>
        <li><svg viewBox="0 0 24 24" aria-hidden="true"><path d="M2 5h20v14H2zm2 2v.5l8 5 8-5V7l-8 5z"/></svg>marcus.k.diet@fernmail.com</li>
        <li><svg viewBox="0 0 24 24" aria-hidden="true"><path d="M12 2a10 10 0 1 0 0 20 10 10 0 0 0 0-20zm-1 17.9A8 8 0 0 1 5.2 8.5L11 14zm6.9-2.6A2 2 0 0 0 16 16h-1v-3a1 1 0 0 0-1-1H8v-2h2a1 1 0 0 0 1-1V7h2a2 2 0 0 0 2-2v-.4a8 8 0 0 1 2.9 12.7z"/></svg>www.brightfieldnutrition.com.au</li>
      </ul>
    </div>

    <p class="title-band">Certified Clinical Nutritionist, Nutritionist and Chef</p>
  </section>

  <section class="card card--back" aria-label="Business card back">
    <p class="back-mark" aria-hidden="true">Brightfield<small>Nutrition &amp; Dietetics</small></p>

    <div class="locations">
      <p class="locations__heading">Consulting at</p>
      <ul class="locations__list">
        <li>Pinebrook Medical Centre</li>
        <li>North Corrin Health</li>
        <li>Hollis Medical</li>
        <li>Ashcombe Doctors Surgery</li>
      </ul>
    </div>

    <div class="appointment">
      <h2 class="appointment__heading">Appointment</h2>
      <p class="field field--date">Date: <span class="field__line" style="width:108px"></span></p>
      <p class="field field--time">Time: <span class="field__line" style="width:108px"></span></p>
      <p class="field field--location">Location: <span class="field__line" style="width:264px"></span></p>
      <p class="appointment__note">If unable to keep appointment, kindly give 24hrs notice.</p>
      <span class="appointment__divider"></span>
      <svg class="appointment__badge" viewBox="0 0 74 78" role="img" aria-label="Certification badge">
        <rect x="0" y="0" width="74" height="78" fill="var(--badge-orange)"/>
      </svg>
    </div>
  </section>

</main>
</body>
</html>
```